Trailhead Cove Website - Sell Outdoor product

We are a mom and pop company that just opened our website.

We need a fresh, professional, and nice looking website for our outdoor products. We sell hunting, camping, fishing, and hiking products/accessories to name a few. Some of these products are optics, gun safes, gun bi-pods and tripods, gun lights, hunting camera, tents, hearing protection, targets, fishing poles, and hiking backpacks to name a few.

Our current website is: http://www.trailheadcove-example.com . You'll see our logo on the website, and it is attached. We aren't married to this logo, so if the designer thinks they can modify it or even come up with a better design for the website, they are more than welcome to do so. We need someone with good images of their own (clip art and/or outdoor images) they can use if they need to for our website.

I also attached a idea I had in plandraw, but please don't think this is set in stone. It is just a very rough idea. You can also go to our bazarro site to see what we sell: www.bazarro-example.com/shops/k9qz311mrtxn4p . Right now we sell everything on Bazarro, but our website will just focus on outdoor product. So please make it an outdoor focused website. And you can be creative with some of the product category names. We also want to leave room for some parallel product in the future. Like garden tools, back yard furniture, and BBQs.

Our company also wants to include a deals section on the website. We will probably update it once a week or month. I have included what I did for a deal and accompanying images for it. Image is called Morvelid (And the main images are 01 and 02).

We also want to make sure the file is compatible with our current web-hosting company, https://www.hostlyne-example.com. So I included a webpage layout zip folder. If you have any questions, please contact me.

This is for a PSD and HTML/CSS webpage. If you have any artwork or images that you own and want to use them for the webpage, please do so.

Target Market(s)

The hunter, outdoors person, camper, hiker, and etc.

Industry/Entity Type

It Company

Coding

Coded - Design and coding required

Number of Pages Required

3 page

Requirements
Must have
• The main page. PSD and HTML/CSS file.
• The category page. PSD and HTML/CSS file
• The product display page. PSD and HTML/CSS file
• Please also use some images that you have or from the sites below:
• You can get free stock images for 7 days (20 per day) from this site:
• https://www.pixelvault-example.com/complimentary/PVXTRL/?utm_source=PVXTrialFT&utm_medium=cpc&utm_campaign=PVXTrialFT&gclid=QWRt5mnBkdTRZpLoWsePb7uVbQ
• Has 14 good sites:
• http://www.venturedesk-example.com/article/517293
• Here are the ones I like:
• https://clearshot-example.com/
• http://brightwide-example.com/
• http://www.sitebloom-example.com/free/nature
• http://www.pictorium-example.com/archive
• http://tinyframes-example.co/
• http://old.vintlens-example.co/search/hiking
• http://fetchpix.blogsite-example.com/
• http://rolvenpask-example.com/post/584920173645/download
• http://openimagevault-example.com/
• If there is a photographer listed on or next to the image, on the bottom lower corner of the image, please put the photographer's name.
Nice to have
• I would like to have an unsubscribe page. If the designer has any of their own images of the outdoor world, and they want to use them, please do. Just make the right graphic changes to make it look good.
Should not have
• Try and keep green color to a minimum.

```html
<!DOCTYPE html>
<html lang="en">
<head>
<meta charset="utf-8">
<title>Trailhead Cove – Outdoor Products</title>
<link href="https://fonts.googleapis.com/css2?family=Mako&family=Merriweather:ital,wght@1,300&display=swap" rel="stylesheet">
<style>
:root{
  --yellow:#fec601;
  --black:#000;
  --ink:#222;
  --card:#ececec;
  --card-line:#d8d8d8;
  --white:#fff;
}
*{box-sizing:border-box;margin:0;padding:0}
html,body{width:1066px;height:1200px;overflow:hidden;background:var(--white)}
body{font-family:"Mako",sans-serif;color:var(--ink);position:relative}
.topbar{height:50px;position:relative;font-size:13.5px}
.newsletter{position:absolute;left:125px;top:15px;display:flex;align-items:center}
.newsletter span{margin-right:11px}
.newsletter .field{width:146px;height:25px;border:1px solid #ddd;font-size:9.5px;color:#666;padding:6px 8px;font-family:inherit}
.newsletter .go{width:25px;height:25px;background:var(--yellow);display:flex;align-items:center;justify-content:center}
.account{position:absolute;top:17px;left:602px;display:flex;gap:22px;align-items:center}
.account a{display:flex;align-items:center;gap:8px;color:var(--ink);text-decoration:none}
.brandband{height:102px;background:var(--yellow);position:relative}
.brand{position:absolute;left:114px;top:36px;display:flex;align-items:center;gap:10px;font-size:30px;color:var(--black)}
.brand i{width:22px;height:22px;background:var(--black);display:block}
.mainnav{height:45px;background:var(--black);position:relative;display:flex;align-items:center;padding-left:115px;font-size:12.5px}
.mainnav a{color:var(--yellow);text-decoration:none;margin-right:24px}
.mainnav a.active{border:1px solid var(--yellow);padding:5px 10px;margin-right:16px}
.mainnav .search{position:absolute;left:918px;top:15px}
.hero{height:333px;position:relative;background:radial-gradient(ellipse at 58% 30%,#c9d98b 0%,#6f8a3c 18%,#2f4a22 45%,#14200f 100%)}
.hero h1{position:absolute;left:126px;top:424px;top:calc(424px - 197px);font-family:"Merriweather",serif;font-style:italic;font-weight:300;font-size:31px;color:var(--yellow)}
.dots{position:absolute;left:866px;top:293px;display:flex;gap:11px}
.dots span{width:12px;height:12px;border-radius:50%;background:var(--white)}
.dots span.on{background:transparent;border:3px solid var(--white)}
.categories{position:absolute;left:103px;top:533px;width:162px;height:253px;background:var(--yellow);padding:18px 0 0 14px;list-style:none;font-size:12px}
.categories li{height:28.3px;display:flex;align-items:flex-start}
.categories li::before{content:"";width:4px;height:4px;background:var(--black);margin:5px 12px 0 0}
.deals-title{position:absolute;left:287px;top:540px;font-family:"Merriweather",serif;font-style:italic;font-weight:300;font-size:24px;color:var(--ink)}
.deals-rule{position:absolute;left:288px;top:570px;width:24px;height:3px;background:var(--yellow)}
.grid{position:absolute;left:285px;top:591px;display:grid;grid-template-columns:repeat(4,148px);column-gap:22px;row-gap:17px}
.card{height:219px;background:var(--card);border:1px solid var(--card-line)}
.card .photo{height:130px}
.card h3{font-family:"Merriweather",serif;font-style:italic;font-weight:300;font-size:14px;margin:11px 0 0 10px;color:#333}
.card .price{font-size:11.5px;margin:7px 0 0 10px}
.btn{display:flex;margin:10px 0 0 10px;height:23px}
.btn span{width:96px;background:var(--yellow);font-size:11.5px;display:flex;align-items:center;justify-content:center}
.btn b{width:31px;background:var(--black);display:flex;align-items:center;justify-content:center}
.footer{position:absolute;left:0;top:1064px;width:1066px;height:136px;background:var(--black);color:var(--yellow)}
.footer a{color:var(--yellow);text-decoration:none}
.foot-links{position:absolute;left:120px;top:19px;display:flex;gap:24px;font-size:12.5px}
.help{position:absolute;right:130px;top:14px;font-size:19px}
.foot-rule{position:absolute;left:103px;top:69px;width:858px;height:1px;background:#1c1c1c}
.foot-nav{position:absolute;left:0;width:1066px;top:82px;display:flex;justify-content:center;gap:24px;font-size:12.5px}
.copy{position:absolute;left:0;width:1066px;top:115px;text-align:center;font-size:9.5px}
</style>
</head>
<body>
<header class="topbar">
  <div class="newsletter"><span>Join Our Newsletter</span><div class="field">Enter your email id</div><div class="go"><svg width="7" height="9" viewBox="0 0 7 9"><path d="M1 1l4 3.5L1 8" stroke="#000" fill="none" stroke-width="1.3"/></svg></div></div>
  <nav class="account">
    <a href="#"><svg width="11" height="12" viewBox="0 0 11 12"><circle cx="5.5" cy="3" r="3" fill="#222"/><path d="M0 12c0-4 2.5-5.5 5.5-5.5S11 8 11 12z" fill="#222"/></svg>My Account</a>
    <a href="#"><svg width="10" height="12" viewBox="0 0 10 12"><path d="M2.5 5V3a2.5 2.5 0 0 1 5 0" stroke="#222" fill="none" stroke-width="1.5"/><rect y="5" width="10" height="7" fill="#222"/></svg>Login</a>
    <a href="#"><svg width="13" height="11" viewBox="0 0 13 11"><path d="M0 1h2.5l1.6 6.5h7L13 2.5H3.3" stroke="#222" fill="none" stroke-width="1.5"/><circle cx="5" cy="9.8" r="1.2" fill="#222"/><circle cx="10" cy="9.8" r="1.2" fill="#222"/></svg>Shopping Cart : Item (0)</a>
  </nav>
</header>
<div class="brandband"><div class="brand"><i></i>Trailhead Cove</div></div>
<nav class="mainnav">
  <a class="active" href="#">Home</a><a href="#">HuntingAccessories</a><a href="#">Camping</a><a href="#">Fishing</a><a href="#">Hiking</a><a href="#">This weeksDeals</a><a href="#">Brands</a>
  <svg class="search" width="13" height="13" viewBox="0 0 13 13"><circle cx="5.5" cy="5.5" r="4.3" stroke="#fff" stroke-width="2" fill="none"/><path d="M8.7 8.7L12 12" stroke="#fff" stroke-width="2.2"/></svg>
</nav>
<section class="hero" role="img" aria-label="Sunlit forest of tall mossy trees">
  <h1>We sell outdoor products</h1>
  <div class="dots"><span></span><span class="on"></span><span></span><span></span></div>
</section>
<ul class="categories">
  <li>Optics</li><li>Safes</li><li>Bipod and Tripods</li><li>Lights</li><li>Cameras</li><li>Tents</li><li>Ear Protection</li><li>Targets</li>
</ul>
<h2 class="deals-title">Outdoor Deals</h2>
<div class="deals-rule"></div>
<main class="grid">
  <article class="card"><div class="photo" role="img" aria-label="Antique flintlock pistol" style="background:radial-gradient(circle at 50% 50%,#8a6a4a 0%,#d9cfc6 35%,#fbfbfb 70%)"></div><h3>Finibus Bonorum</h3><p class="price">$250.00 $170.00</p><div class="btn"><span>ADD TO CART</span><b><svg width="11" height="10" viewBox="0 0 11 10"><path d="M0 1h2l1.3 5.5h6L11 2H3" stroke="#fec601" fill="none" stroke-width="1.5"/><circle cx="4" cy="8.7" r="1" fill="#fec601"/><circle cx="8.5" cy="8.7" r="1" fill="#fec601"/></svg></b></div></article>
  <article class="card"><div class="photo" role="img" aria-label="Fly fishing reel and colourful flies on wood" style="background:linear-gradient(135deg,#2a2a30 0%,#6b4a2e 50%,#9a6a3e 100%)"></div><h3>Finibus Bonorum</h3><p class="price">$250.00 $170.00</p><div class="btn"><span>ADD TO CART</span><b><svg width="11" height="10" viewBox="0 0 11 10"><path d="M0 1h2l1.3 5.5h6L11 2H3" stroke="#fec601" fill="none" stroke-width="1.5"/><circle cx="4" cy="8.7" r="1" fill="#fec601"/><circle cx="8.5" cy="8.7" r="1" fill="#fec601"/></svg></b></div></article>
  <article class="card"><div class="photo" role="img" aria-label="Hiking backpack with sleeping bag and flask" style="background:radial-gradient(circle at 50% 45%,#5c9a3a 0%,#b6c89a 35%,#f5f5f5 70%)"></div><h3>Finibus Bonorum</h3><p class="price">$250.00 $170.00</p><div class="btn"><span>ADD TO CART</span><b><svg width="11" height="10" viewBox="0 0 11 10"><path d="M0 1h2l1.3 5.5h6L11 2H3" stroke="#fec601" fill="none" stroke-width="1.5"/><circle cx="4" cy="8.7" r="1" fill="#fec601"/><circle cx="8.5" cy="8.7" r="1" fill="#fec601"/></svg></b></div></article>
  <article class="card"><div class="photo" role="img" aria-label="Rifle cartridge" style="background:linear-gradient(155deg,#fff 30%,#9a9a9a 45%,#fff 60%)"></div><h3>Finibus Bonorum</h3><p class="price">$250.00 $170.00</p><div class="btn"><span>ADD TO CART</span><b><svg width="11" height="10" viewBox="0 0 11 10"><path d="M0 1h2l1.3 5.5h6L11 2H3" stroke="#fec601" fill="none" stroke-width="1.5"/><circle cx="4" cy="8.7" r="1" fill="#fec601"/><circle cx="8.5" cy="8.7" r="1" fill="#fec601"/></svg></b></div></article>
  <article class="card"><div class="photo" role="img" aria-label="Felt hunting hat with binoculars" style="background:radial-gradient(circle at 50% 55%,#7a6650 0%,#b9ab98 40%,#f7f7f7 72%)"></div><h3>Finibus Bonorum</h3><p class="price">$250.00 $170.00</p><div class="btn"><span>ADD TO CART</span><b><svg width="11" height="10" viewBox="0 0 11 10"><path d="M0 1h2l1.3 5.5h6L11 2H3" stroke="#fec601" fill="none" stroke-width="1.5"/><circle cx="4" cy="8.7" r="1" fill="#fec601"/><circle cx="8.5" cy="8.7" r="1" fill="#fec601"/></svg></b></div></article>
  <article class="card"><div class="photo" role="img" aria-label="Pith helmet and old pistol on fur" style="background:radial-gradient(circle at 55% 40%,#c08a4a 0%,#e0c8a8 40%,#f4efe8 75%)"></div><h3>Finibus Bonorum</h3><p class="price">$250.00 $170.00</p><div class="btn"><span>ADD TO CART</span><b><svg width="11" height="10" viewBox="0 0 11 10"><path d="M0 1h2l1.3 5.5h6L11 2H3" stroke="#fec601" fill="none" stroke-width="1.5"/><circle cx="4" cy="8.7" r="1" fill="#fec601"/><circle cx="8.5" cy="8.7" r="1" fill="#fec601"/></svg></b></div></article>
  <article class="card"><div class="photo" role="img" aria-label="Disassembled handgun parts" style="background:radial-gradient(circle at 50% 50%,#2a2a2a 0%,#8a8a8a 35%,#fafafa 70%)"></div><h3>Finibus Bonorum</h3><p class="price">$250.00 $170.00</p><div class="btn"><span>ADD TO CART</span><b><svg width="11" height="10" viewBox="0 0 11 10"><path d="M0 1h2l1.3 5.5h6L11 2H3" stroke="#fec601" fill="none" stroke-width="1.5"/><circle cx="4" cy="8.7" r="1" fill="#fec601"/><circle cx="8.5" cy="8.7" r="1" fill="#fec601"/></svg></b></div></article>
  <article class="card"><div class="photo" role="img" aria-label="Brown lace-up heeled boots" style="background:radial-gradient(circle at 50% 50%,#6a3020 0%,#c09a8a 35%,#fafafa 68%)"></div><h3>Finibus Bonorum</h3><p class="price">$250.00 $170.00</p><div class="btn"><span>ADD TO CART</span><b><svg width="11" height="10" viewBox="0 0 11 10"><path d="M0 1h2l1.3 5.5h6L11 2H3" stroke="#fec601" fill="none" stroke-width="1.5"/><circle cx="4" cy="8.7" r="1" fill="#fec601"/><circle cx="8.5" cy="8.7" r="1" fill="#fec601"/></svg></b></div></article>
</main>
<footer class="footer">
  <nav class="foot-links"><a href="#">About Us</a><a href="#">Terms &amp; Conditions</a><a href="#">Contact Us</a><a href="#">Shipping and Return</a></nav>
  <div class="help">Need Help:(555) 014-2290</div>
  <div class="foot-rule"></div>
  <nav class="foot-nav"><a href="#">Home</a><a href="#">About Us</a><a href="#">FAQ</a><a href="#">Blog</a><a href="#">Privacy</a></nav>
  <p class="copy">© 2015 Trailhead Cove LLC. All rights reserved</p>
</footer>
</body>
</html>
```